Business Cards for new orthopaedic surgery practice

My husband and I are starting our own orthopaedic surgery practice. We are looking for a business card that is uniform, but one will have my name/title and the other will have his. You can just create one design with my name on it for now. But when I choose your design as the winning design I will ask that you add another copy with his name/title.

We are looking for classy, simple, elite all in one. We like dark blues/a little gold/yellow. Something that goes with our logo. We want our logo incorporated. Here is all the info you need:
Business name: RV Bone & Vitality Center
Location: 38517 North Willowmere Ave
Maple Hollow, FL 33988
Phone: 954-218-4063
Fax: 954-582-7341
Email: info@myrvbonecare.example

Names: Lydia Vance, M.D.
Board Certified Hand and Upper Extremity Surgeon

Ebo Dansu, M.D.
Board Certified Hip & Knee Replacement/General Orthopaedic Surgeon

Can decide what you want to put on the back. Maybe a slogan:
Rooted in Care. Focused on You

I am just going to upload our logo. The only thing is if we select you as the winning design, the location, and phone numbers may change. We will need your help to update that once fully solidified.

Industry/Entity Type

Medical

Contact Information for Business Card

Colors
0054AA
0677BA
7BADD7
CADEEF
E8F1F8
0094D4
00A9DD
6FCCEA
C7EBF8
E9F6FB

Requirements
Must have
• class, appeal,
Should not have
• We want to air on the side of masculine if we are looking at masculine vs. feminine feel. But we still want it classy, sophisticated, and something we will love

```html
<!DOCTYPE html>
<html lang="en">
<head>
<meta charset="utf-8">
<title>RV Bone &amp; Vitality Center – Business Card</title>
<link rel="stylesheet" href="https://fonts.googleapis.com/css2?family=Cabin:wght@400;500&family=Ubuntu:wght@500;700&display=swap">
<style>
  :root {
    --page-bg: #e4e5e7;
    --card-white: #ffffff;
    --navy-top: #233a78;
    --navy-top-deep: #1c2d63;
    --navy-bottom: #3659a8;
    --wing-deep: #06238c;
    --wing-soft: #2b4a93;
    --accent-cyan: #1fb7df;
    --ink-navy: #26357a;
  }
  * { margin: 0; padding: 0; box-sizing: border-box; }
  html, body { width: 1200px; height: 1200px; overflow: hidden; }
  body { background: var(--page-bg); position: relative; font-family: "Cabin", sans-serif; }

  .card {
    position: absolute;
    left: 203px;
    width: 793px;
    height: 453px;
    border-radius: 50px;
    overflow: hidden;
    background: var(--card-white);
  }
  .card--front { top: 102px; }
  .card--back { top: 644px; }

  .card__band { position: absolute; inset: 0; width: 100%; height: 100%; }

  .brand-name {
    position: absolute;
    top: 168px;
    left: 0; right: 0;
    text-align: center;
    font-family: "Ubuntu", sans-serif;
    font-weight: 500;
    font-size: 32px;
    line-height: 38px;
    letter-spacing: 1px;
    color: var(--card-white);
    text-transform: uppercase;
  }

  .tagline {
    position: absolute;
    top: 383px;
    left: 0; right: 0;
    text-align: center;
    font-family: "Ubuntu", sans-serif;
    font-weight: 700;
    font-size: 24px;
    color: var(--accent-cyan);
    letter-spacing: 0.2px;
  }

  .doctor-name {
    position: absolute;
    top: 84px;
    left: 0; right: 0;
    text-align: center;
    font-family: "Ubuntu", sans-serif;
    font-weight: 700;
    font-size: 22px;
    color: var(--card-white);
    text-transform: uppercase;
  }
  .doctor-title {
    position: absolute;
    top: 121px;
    left: 0; right: 0;
    text-align: center;
    font-family: "Cabin", sans-serif;
    font-weight: 400;
    font-size: 21px;
    color: var(--accent-cyan);
  }

  .contact-icon {
    position: absolute;
    width: 36px;
    height: 36px;
    border: 2px solid var(--accent-cyan);
    display: flex;
    align-items: center;
    justify-content: center;
  }
  .contact-icon svg { width: 18px; height: 18px; }
  .contact-text {
    position: absolute;
    font-family: "Cabin", sans-serif;
    font-weight: 500;
    font-size: 21px;
    line-height: 26px;
    color: var(--ink-navy);
  }
</style>
</head>
<body>

<section class="card card--front">
  <svg class="card__band" viewBox="0 0 1277 730" preserveAspectRatio="none" aria-hidden="true">
    <defs>
      <linearGradient id="frontNavy" x1="0" y1="0" x2="0" y2="1">
        <stop offset="0" stop-color="var(--navy-top)"/>
        <stop offset="1" stop-color="var(--navy-bottom)"/>
      </linearGradient>
      <linearGradient id="frontWing" x1="0" y1="0" x2="0" y2="1">
        <stop offset="0" stop-color="var(--wing-deep)"/>
        <stop offset="0.6" stop-color="var(--wing-soft)"/>
      </linearGradient>
    </defs>
    <polygon points="0,0 1277,0 1277,531 960,444 642,531 325,444 0,533" fill="url(#frontNavy)"/>
    <polygon points="0,356 325,444 0,533" fill="url(#frontWing)"/>
    <polygon points="1277,356 960,444 1277,531" fill="url(#frontWing)"/>
  </svg>
  <h1 class="brand-name">RV Bone &amp; Vitality<br>Center</h1>
  <p class="tagline">GROUNDED IN CARE. CENTERED ON YOU.</p>
</section>

<section class="card card--back">
  <svg class="card__band" viewBox="0 0 1277 730" preserveAspectRatio="none" aria-hidden="true">
    <defs>
      <linearGradient id="backNavy" x1="0" y1="0" x2="0" y2="1">
        <stop offset="0" stop-color="var(--navy-top-deep)"/>
        <stop offset="0.61" stop-color="var(--navy-bottom)"/>
      </linearGradient>
      <linearGradient id="backWing" x1="0" y1="0" x2="0" y2="1">
        <stop offset="0" stop-color="var(--wing-deep)"/>
        <stop offset="0.6" stop-color="var(--wing-soft)"/>
      </linearGradient>
    </defs>
    <polygon points="0,0 1277,0 1277,443 960,356 642,443 325,356 0,445" fill="url(#backNavy)"/>
    <polygon points="0,268 325,356 0,445" fill="url(#backWing)"/>
    <polygon points="1277,268 960,356 1277,443" fill="url(#backWing)"/>
  </svg>

  <h2 class="doctor-name">Lydia Vance, M.D.</h2>
  <p class="doctor-title">Board Certified Hand and Upper Extremity Surgeon</p>

  <span class="contact-icon" style="left:78px; top:314px;">
    <svg viewBox="0 0 24 24"><path fill="var(--accent-cyan)" d="M6.6 10.8c1.4 2.8 3.8 5.1 6.6 6.6l2.2-2.2c.3-.3.7-.4 1-.2 1.1.4 2.3.6 3.6.6.6 0 1 .4 1 1V20c0 .6-.4 1-1 1C10.6 21 3 13.4 3 4c0-.6.4-1 1-1h3.5c.6 0 1 .4 1 1 0 1.3.2 2.5.6 3.6.1.3 0 .7-.2 1L6.6 10.8z"/></svg>
  </span>
  <span class="contact-text" style="left:131px; top:319px;">954-218-4063</span>

  <span class="contact-icon" style="left:78px; top:360px;">
    <svg viewBox="0 0 24 24" fill="none" stroke="var(--accent-cyan)" stroke-width="1.8"><rect x="7" y="3" width="10" height="6"/><rect x="3" y="9" width="18" height="8" rx="1"/><rect x="7" y="14" width="10" height="7"/></svg>
  </span>
  <span class="contact-text" style="left:131px; top:365px;">954-582-7341</span>

  <span class="contact-icon" style="left:433px; top:314px;">
    <svg viewBox="0 0 24 24"><path fill="var(--accent-cyan)" d="M12 2c-3.9 0-7 3.1-7 7 0 5.2 7 13 7 13s7-7.8 7-13c0-3.9-3.1-7-7-7zm0 9.5c-1.4 0-2.5-1.1-2.5-2.5S10.6 6.5 12 6.5s2.5 1.1 2.5 2.5-1.1 2.5-2.5 2.5z"/></svg>
  </span>
  <span class="contact-text" style="left:478px; top:319px;">info@myrvbonecare.example</span>

  <span class="contact-icon" style="left:433px; top:360px;">
    <svg viewBox="0 0 24 24"><path fill="var(--accent-cyan)" d="M3 6h18v12H3z"/><path fill="none" stroke="#fff" stroke-width="1.5" d="M3 6l9 7 9-7M3 18l7-6M21 18l-7-6"/></svg>
  </span>
  <span class="contact-text" style="left:484px; top:365px;">38517 North Willowmere Ave<br>Maple Hollow, FL 33988</span>
</section>

</body>
</html>
```